We are a local Communty Pharmacy wishing to promote and market a specialised Pharmaceutical Service

We would like a design that is professional and enticing ( according to the brief In attached files)
We wish to Market Compounding Pharmacy as a specialist side of our business.
We have the expertise a purpose built preparation laboratory.
The main purpose is an Internet presence that entices prospective patients to contact or visit our physical store.

Target Market(s)

Patients Medicos and Veterinary clients

Industry/Entity Type

Pharmacy

Coding

Coded - Design and coding required

Number of Pages Required

1 page

Requirements
Must have
• Clear friendly image
Nice to have
• soft enticing feel
Should not have
• No crass loud unprofessional elements

```html
<!DOCTYPE html>
<html lang="en">
<head>
<meta charset="utf-8">
<title>Westvale Compounding Pharmacy</title>
<link href="https://fonts.googleapis.com/css2?family=Open+Sans:wght@400;600;700;800&display=swap" rel="stylesheet">
<style>
:root{
  --navy:#123a66;
  --navy-dark:#0d2c4f;
  --blue:#1f8fd6;
  --sky:#2aa0e0;
  --yellow:#f5b81c;
  --green:#3bb26a;
  --red:#ec5a4a;
  --grey-band:#eef1f4;
  --text:#6c7480;
  --heading:#2a3440;
  --white:#ffffff;
}
*{box-sizing:border-box;margin:0;padding:0}
html,body{width:1200px;height:2392px;overflow:hidden}
body{font-family:"Open Sans",Arial,sans-serif;color:var(--text);background:var(--white);font-size:14px}
.topbar{height:32px;background:var(--navy);color:#cfe0f2;font-size:11px;display:flex;align-items:center;padding:0 48px;gap:40px}
.topbar .right{margin-left:auto}
.header{height:120px;display:flex;align-items:center;padding:0 48px;border-bottom:1px solid #e3e7ec}
.brand{display:flex;align-items:center;gap:12px}
.brand .mark{width:40px;height:40px;border-radius:50%;background:var(--blue)}
.brand .name{font-weight:800;font-size:22px;color:var(--navy);line-height:1.1}
.nav{margin-left:auto;display:flex;gap:34px;font-size:12px;font-weight:600;color:#5d6672}
.nav .contact{background:var(--yellow);color:var(--white);padding:8px 16px;border-radius:3px}
.hero{height:448px;position:relative;background:linear-gradient(120deg,#cfe6f5 0%,#8cc3e6 45%,#3a7fb8 100%)}
.hero .lines{position:absolute;left:100px;top:200px}
.hero .lines span{display:block;color:var(--white);font-weight:700;padding:10px 28px;margin-bottom:10px}
.hero .l1{background:var(--yellow);font-size:26px;width:max-content}
.hero .l2{background:var(--blue);font-size:22px;width:max-content}
.services{background:var(--grey-band);height:380px;display:flex;justify-content:center;gap:30px;padding-top:40px}
.svc{width:240px;height:300px;color:var(--white);text-align:center;padding:40px 24px 0;position:relative}
.svc .icon{width:74px;height:74px;border-radius:50%;background:var(--white);margin:0 auto 18px;display:flex;align-items:center;justify-content:center}
.svc h3{font-size:15px;margin-bottom:8px}
.svc p{font-size:11px;line-height:1.5}
.svc .more{display:inline-block;margin-top:18px;background:rgba(0,0,0,.22);font-size:10px;font-weight:700;padding:7px 16px}
.blue{background:var(--blue)}.yellow{background:var(--yellow)}.green{background:var(--green)}.red{background:var(--red)}
.about{padding:80px 100px 0;height:640px}
.section-title{text-align:center;font-size:22px;font-weight:800;color:var(--heading);letter-spacing:.5px}
.section-title::after{content:"";display:block;width:60px;height:3px;background:var(--yellow);margin:14px auto 0}
.about .cols{display:flex;gap:50px;margin-top:40px;font-size:12px;line-height:1.9}
.about .cols div{flex:1}
.about .cols p+p{margin-top:14px}
.btn{display:inline-block;background:var(--yellow);color:var(--white);font-weight:700;font-size:12px;padding:14px 26px;margin-top:60px}
.features{padding:0 100px;height:400px}
.features .head{display:flex;justify-content:space-between;align-items:center;border-bottom:1px solid #e3e7ec;padding-bottom:12px}
.features h2{font-size:18px;font-weight:800;color:var(--heading)}
.arrows{display:flex;gap:6px}
.arrows span{width:20px;height:20px;background:#d5dbe2;display:block}
.cards{display:flex;gap:40px;margin-top:24px}
.card{flex:1}
.card .photo{height:180px;background:linear-gradient(135deg,#e9eef3,#b9c9d8)}
.card h4{color:var(--blue);font-size:13px;margin:14px 0 6px}
.card p{font-size:11px;line-height:1.6}
.footer{background:var(--navy);height:340px;color:#c4d3e4;display:flex;gap:50px;padding:40px 100px 0;font-size:11px}
.footer h5{color:var(--white);font-size:13px;margin-bottom:16px}
.footer .col{flex:1}
.hours td{padding:3px 0}
.hours td:last-child{text-align:right}
.hours{width:100%;border-collapse:collapse}
.map{height:200px;background:linear-gradient(135deg,#dfe7d9,#c9d6e2)}
.contact-row{display:flex;gap:10px;margin-bottom:14px;line-height:1.5}
.contact-row svg{flex:none}
.bottombar{height:32px;background:var(--navy-dark);color:#8ea6c2;font-size:10px;display:flex;align-items:center;padding:0 100px}
.bottombar .right{margin-left:auto}
</style>
</head>
<body>
<div class="topbar"><span>14 Harbour Lane, Westvale WA 6100</span><span>(08) 5550 1234</span><span class="right">hello@westvalepharmacy.example</span></div>
<header class="header">
  <div class="brand"><span class="mark"></span><div class="name">WESTVALE<br><span style="font-size:12px;font-weight:600;color:var(--blue)">Compounding Pharmacy</span></div></div>
  <nav class="nav"><span>HOME</span><span>ABOUT US</span><span>LOCATIONS</span><span>TERMS</span><span class="contact">CONTACT</span></nav>
</header>
<section class="hero" role="img" aria-label="Photo of a pharmacy preparation laboratory with glassware">
  <div class="lines"><span class="l1">COMPOUNDING PHARMACY</span><span class="l2">CUSTOMISED MEDICATIONS FOR PATIENTS</span></div>
</section>
<section class="services">
  <div class="svc blue"><div class="icon"><svg width="36" height="36" viewBox="0 0 36 36"><rect x="8" y="6" width="20" height="26" rx="3" fill="none" stroke="#1f8fd6" stroke-width="3"/><path d="M13 14h10M13 20h10M13 26h6" stroke="#1f8fd6" stroke-width="3"/></svg></div><h3>Contrary to popular</h3><p>It is a long established fact that a reader will be distracted by the readable content of a page when looking at its layout.</p><span class="more">MORE INFO</span></div>
  <div class="svc yellow"><div class="icon"><svg width="36" height="36" viewBox="0 0 36 36"><path d="M14 4h8v10l8 16H6l8-16z" fill="none" stroke="#f5b81c" stroke-width="3"/></svg></div><h3>Contrary to popular</h3><p>It is a long established fact that a reader will be distracted by the readable content of a page when looking at its layout.</p><span class="more">MORE INFO</span></div>
  <div class="svc green"><div class="icon"><svg width="36" height="36" viewBox="0 0 36 36"><circle cx="18" cy="26" r="6" fill="none" stroke="#3bb26a" stroke-width="3"/><path d="M18 20V6M12 8l12 6" stroke="#3bb26a" stroke-width="3"/></svg></div><h3>Contrary to popular</h3><p>It is a long established fact that a reader will be distracted by the readable content of a page when looking at its layout.</p><span class="more">MORE INFO</span></div>
  <div class="svc red"><div class="icon"><svg width="36" height="36" viewBox="0 0 36 36"><rect x="4" y="12" width="28" height="12" rx="6" fill="none" stroke="#ec5a4a" stroke-width="3" transform="rotate(-35 18 18)"/></svg></div><h3>Contrary to popular</h3><p>It is a long established fact that a reader will be distracted by the readable content of a page when looking at its layout.</p><span class="more">MORE INFO</span></div>
</section>
<section class="about">
  <h2 class="section-title">WHAT IS COMPOUNDING PHARMACY?</h2>
  <div class="cols">
    <div><p>Compounding is the practice of preparing medicines to suit the needs of an individual patient. It was once the everyday work of every pharmacist, before mass manufacture made standard doses the norm for most people.</p><p>Today our pharmacists prepare creams, capsules, liquids and lozenges in our purpose built laboratory, adjusting strength, flavour and form so that each patient receives a medicine that fits them.</p></div>
    <div><p>As a dedicated service within our community pharmacy, we work closely with doctors, specialists and veterinarians to create formulations that are not available off the shelf, always prepared to strict quality standards.</p><p>Whether you need a dye free tablet, a sugar free syrup, or a dose measured for a small pet, our team is here to help. Visit our store or contact us to talk through your needs with a pharmacist.</p></div>
  </div>
  <span class="btn">READ MORE INFO</span>
</section>
<section class="features">
  <div class="head"><h2>FEATURE ITEMS</h2><div class="arrows"><span></span><span></span></div></div>
  <div class="cards">
    <div class="card"><div class="photo" role="img" aria-label="Photo of a veterinarian examining a pet"></div><h4>EXAMPLE VET ARTICLE</h4><p>Find out how tailored medicines help pets take their treatment with less stress and more comfort.</p></div>
    <div class="card"><div class="photo" role="img" aria-label="Photo of a patient receiving care"></div><h4>EXAMPLE SCAR THERAPY</h4><p>Find out how custom topical preparations can support healing and comfort for sensitive skin.</p></div>
    <div class="card"><div class="photo" role="img" aria-label="Photo of a consultation about thyroid care"></div><h4>EXAMPLE THYROID EXTRACT</h4><p>Find out how measured doses prepared in our lab can be matched to each patient's needs.</p></div>
  </div>
</section>
<footer class="footer">
  <div class="col"><h5>PHARMACY NEWS</h5>
    <table class="hours">
      <tr><td>Monday</td><td>7:00 am - 7:30 pm</td></tr>
      <tr><td>Tuesday</td><td>7:00 am - 7:30 pm</td></tr>
      <tr><td>Wednesday</td><td>7:00 am - 7:30 pm</td></tr>
      <tr><td>Thursday</td><td>7:00 am - 7:30 pm</td></tr>
      <tr><td>Friday</td><td>7:00 am - 7:30 pm</td></tr>
      <tr><td>Saturday</td><td>8:00 am - 5:00 pm</td></tr>
      <tr><td>Sunday</td><td>9:00 am - 5:00 pm</td></tr>
    </table>
  </div>
  <div class="col"><h5>LOCATIONS</h5><div class="map" role="img" aria-label="Map showing the pharmacy location"></div></div>
  <div class="col"><h5>CONTACT INFO</h5>
    <div class="contact-row"><span>Visit our store to speak with a pharmacist about your compounded medicine.</span></div>
    <div class="contact-row"><svg width="14" height="14" viewBox="0 0 14 14"><path d="M7 1a4 4 0 0 1 4 4c0 3-4 8-4 8S3 8 3 5a4 4 0 0 1 4-4z" fill="#f5b81c"/></svg><span>14 Harbour Lane, Westvale WA 6100</span></div>
    <div class="contact-row"><svg width="14" height="14" viewBox="0 0 14 14"><path d="M3 1l3 3-2 2a8 8 0 0 0 4 4l2-2 3 3-2 2C6 13 1 8 1 3z" fill="#f5b81c"/></svg><span>(08) 5550 1234</span></div>
    <div class="contact-row"><svg width="14" height="14" viewBox="0 0 14 14"><rect x="1" y="3" width="12" height="8" fill="none" stroke="#f5b81c" stroke-width="1.5"/><path d="M1 3l6 5 6-5" fill="none" stroke="#f5b81c" stroke-width="1.5"/></svg><span>hello@westvalepharmacy.example</span></div>
  </div>
</footer>
<div class="bottombar"><span>© 2024 Westvale Compounding Pharmacy. All rights reserved.</span><span class="right">Privacy Policy · Terms</span></div>
</body>
</html>
```